Board Presentation template

Design a simple and clean PowerPoint slide templates for a Board meeting. The slides should have predominantly white backgrounds and use the colors of our Logo (attached): Tones of grey and orange and blue.
The company name is called Keystone Lane Gauging.
It sell, calibrate, service and repair industrial and commercial scales of all types. In particular, Truck scales, floor scales, counting scales and benchtop scales.
There is no website for Keystone Lane Gauging, but we have three affiliates that have their own websites:
https://www.fernwaybalance.example/
https://meadowlarkhandlingandmassing.example/
https://tvbalance.example/
Target Market(s)
Industrial and Commercial Weighing systems
Industry/Entity Type
Look and feel

```html
<!DOCTYPE html>
<html lang="en">
<head>
<meta charset="utf-8">
<title>Keystone Lane Gauging – Board Presentation Templates</title>
<link href="https://fonts.googleapis.com/css2?family=Oswald:wght@400;500;600;700&family=Poppins:wght@400;500;600;700&display=swap" rel="stylesheet">
<style>
  :root{
    --canvas:#c9cacc;
    --white:#ffffff;
    --ink:#343d46;
    --ink-soft:#4a525a;
    --blue:#1f4b7a;
    --red:#c0272d;
    --card:#f2f1f4;
    --rule:#3b434b;
    --photo-dark:#2f3a44;
  }
  *{box-sizing:border-box;margin:0;padding:0}
  html,body{width:1016px;height:1200px;overflow:hidden;background:var(--canvas)}
  body{position:relative;font-family:"Poppins",sans-serif;color:var(--ink)}
  .slide{position:absolute;width:434px;height:244px;background:var(--white);overflow:hidden}
  .col-left{left:72px}
  .col-right{left:532px}
  .row-1{top:74px}
  .row-2{top:340px}
  .row-3{top:605px}
  .row-4{top:872px}

  .mesh-fade{position:absolute;left:0;right:0;bottom:0;height:110px;
    background:linear-gradient(180deg,rgba(220,226,236,0) 0%,rgba(214,221,233,.55) 100%)}

  /* shared slide header */
  .brand-mini{position:absolute;left:6px;top:12px;width:44px;font-family:"Oswald",sans-serif;font-weight:500;
    font-size:5.6px;line-height:1.15;text-align:center;color:var(--ink);letter-spacing:.2px}
  .head-divider{position:absolute;left:53px;top:6px;width:1px;height:34px;background:#555d64}
  .head-title{position:absolute;left:66px;top:13px;font-family:"Oswald",sans-serif;font-weight:600;font-size:11px;color:var(--ink);letter-spacing:.2px}

  /* title slide */
  .title-slide .top-bar{position:absolute;left:0;top:0;width:100%;height:5px;background:var(--ink)}
  .title-slide .brand-mark{position:absolute;left:0;right:0;top:68px;text-align:center;font-family:"Oswald",sans-serif;
    font-weight:500;font-size:14px;color:var(--ink);letter-spacing:.4px}
  .title-slide .deck-title{position:absolute;left:0;right:0;top:112px;text-align:center;font-family:"Oswald",sans-serif;
    font-weight:700;font-size:21px;color:var(--ink);letter-spacing:.3px}
  .title-slide .meeting-badge{position:absolute;left:125px;top:158px;width:184px;height:26px;background:var(--blue);color:var(--white);
    font-family:"Oswald",sans-serif;font-weight:600;font-size:13px;line-height:26px;text-align:center;letter-spacing:.2px}
  .title-slide .meeting-date{position:absolute;left:0;right:0;top:201px;text-align:center;font-family:"Oswald",sans-serif;
    font-weight:600;font-size:11px;color:var(--red)}

  /* agenda */
  .agenda-list{position:absolute;left:24px;top:56px;width:384px;list-style:none}
  .agenda-item{position:relative;height:22.6px;border-bottom:1px solid var(--rule);font-family:"Oswald",sans-serif;font-size:8px;
    line-height:22px;color:var(--ink);padding-left:26px}
  .agenda-item:last-child{border-bottom:none}
  .agenda-item svg{position:absolute;left:7px;top:7px}
  .agenda-page{position:absolute;right:0;top:0}

  /* section divider */
  .section-slide .brand-mark{position:absolute;left:0;right:0;top:30px;text-align:center;font-family:"Oswald",sans-serif;
    font-weight:500;font-size:14px;color:var(--ink);letter-spacing:.4px}
  .section-slide .section-photo{position:absolute;left:0;top:76px;width:100%;height:168px;
    background:linear-gradient(180deg,#3a4550 0%,#2f3943 100%)}
  .section-slide .section-title{position:absolute;left:0;right:0;top:111px;text-align:center;font-family:"Oswald",sans-serif;
    font-weight:400;font-size:31px;color:var(--white);letter-spacing:.5px}
  .section-slide .section-sub{position:absolute;left:0;right:0;top:158px;text-align:center;font-weight:600;font-size:6.4px;color:var(--white)}

  /* services */
  .service-card{position:absolute;width:132px;background:var(--card);border-radius:8px;padding:10px 12px 0 13px}
  .service-card h3{font-weight:600;font-size:6.6px;color:#222;margin-bottom:5px}
  .service-card p{font-size:4.3px;line-height:1.55;color:#444}
  .service-icon{position:absolute;right:-4px;top:-5px;width:21px;height:21px;border-radius:50%;background:var(--red);
    border:2px solid var(--white);box-shadow:0 0 0 .5px #ddd;display:flex;align-items:center;justify-content:center}

  /* about */
  .about-copy{position:absolute;left:12px;width:208px;font-size:4.35px;line-height:1.75;text-align:justify;color:#333}
  .about-photo{position:absolute;left:237px;top:0;width:197px;height:244px;background:linear-gradient(160deg,#dfe5ea 0%,#b8c2cb 55%,#7d8891 100%)}

  /* process */
  .process-line{position:absolute;left:0;top:0}
  .step-badge{position:absolute;width:17px;height:20px;background:var(--ink);color:var(--white);font-weight:600;font-size:7.5px;
    text-align:center;line-height:15px;clip-path:polygon(0 0,100% 0,100% 72%,50% 100%,0 72%)}
  .step{position:absolute;width:94px}
  .step h4{font-weight:500;font-size:8px;color:#111;margin-bottom:3px}
  .step p{font-size:4.2px;line-height:1.55;color:#333}

  /* feature slide */
  .feature-rail{position:absolute;left:19px;top:60px;width:1px;height:172px;background:#555}
  .feature-title{position:absolute;left:46px;top:56px;font-size:17px;line-height:1.25;color:#111}
  .feature-title strong{display:block;color:var(--red);font-weight:600}
  .feature-points{position:absolute;left:19px;top:118px;list-style:none;width:200px}
  .feature-points li{position:relative;padding-left:42px;font-size:6.1px;line-height:1.3;color:#222;height:27.5px}
  .feature-points li::before{content:"";position:absolute;left:0;top:5px;width:22px;height:1px;background:#555}
  .feature-points li::after{content:"";position:absolute;left:30px;top:3.5px;width:3px;height:3px;border-radius:50%;background:#222}
  .feature-photo{position:absolute;left:0;top:0}

  /* closing */
  .closing-slide .brand-mark{position:absolute;left:0;right:0;top:70px;text-align:center;font-family:"Oswald",sans-serif;
    font-weight:500;font-size:14px;color:var(--ink);letter-spacing:.4px}
  .closing-slide .thanks{position:absolute;left:0;right:0;top:124px;text-align:center;font-family:"Oswald",sans-serif;
    font-weight:700;font-size:39px;color:var(--ink);letter-spacing:.5px}
  .closing-slide .thanks span{color:var(--red)}
</style>
</head>
<body>

<!-- Title -->
<section class="slide title-slide col-left row-1">
  <div class="mesh-fade"></div>
  <div class="top-bar"></div>
  <div class="brand-mark">KEYSTONE LANE GAUGING</div>
  <h1 class="deck-title">KEYSTONE LANE GAUGING</h1>
  <div class="meeting-badge">BOARD OF DIRECTORS MEETING</div>
  <div class="meeting-date">OCTOBER 2025</div>
</section>

<!-- Agenda -->
<section class="slide agenda-slide col-right row-1">
  <div class="brand-mini">KEYSTONE LANE<br>GAUGING</div>
  <div class="head-divider"></div>
  <h2 class="head-title">AGENDA</h2>
  <ul class="agenda-list">
    <li class="agenda-item"><svg width="9" height="8" viewBox="0 0 9 8"><path d="M1 4.2 3.4 6.6 8 1.2" fill="none" stroke="#c0272d" stroke-width="1.8"/></svg>Company Overview<span class="agenda-page">02</span></li>
    <li class="agenda-item"><svg width="9" height="8" viewBox="0 0 9 8"><path d="M1 4.2 3.4 6.6 8 1.2" fill="none" stroke="#c0272d" stroke-width="1.8"/></svg>Financial Performance<span class="agenda-page">03</span></li>
    <li class="agenda-item"><svg width="9" height="8" viewBox="0 0 9 8"><path d="M1 4.2 3.4 6.6 8 1.2" fill="none" stroke="#c0272d" stroke-width="1.8"/></svg>Operations &amp; Service Metrics<span class="agenda-page">04</span></li>
    <li class="agenda-item"><svg width="9" height="8" viewBox="0 0 9 8"><path d="M1 4.2 3.4 6.6 8 1.2" fill="none" stroke="#c0272d" stroke-width="1.8"/></svg>Sales &amp; Market Insights<span class="agenda-page">05</span></li>
    <li class="agenda-item"><svg width="9" height="8" viewBox="0 0 9 8"><path d="M1 4.2 3.4 6.6 8 1.2" fill="none" stroke="#c0272d" stroke-width="1.8"/></svg>Strategic Initiatives<span class="agenda-page">06</span></li>
    <li class="agenda-item"><svg width="9" height="8" viewBox="0 0 9 8"><path d="M1 4.2 3.4 6.6 8 1.2" fill="none" stroke="#c0272d" stroke-width="1.8"/></svg>Challenges &amp; Risk Management<span class="agenda-page">07</span></li>
    <li class="agenda-item"><svg width="9" height="8" viewBox="0 0 9 8"><path d="M1 4.2 3.4 6.6 8 1.2" fill="none" stroke="#c0272d" stroke-width="1.8"/></svg>Future Roadmap<span class="agenda-page">08</span></li>
    <li class="agenda-item"><svg width="9" height="8" viewBox="0 0 9 8"><path d="M1 4.2 3.4 6.6 8 1.2" fill="none" stroke="#c0272d" stroke-width="1.8"/></svg>Closing &amp; Q&amp;A<span class="agenda-page">09</span></li>
  </ul>
</section>

<!-- Section divider -->
<section class="slide section-slide col-left row-2">
  <div class="brand-mark">KEYSTONE LANE GAUGING</div>
  <div class="section-photo" role="img" aria-label="Dimmed photo of a team meeting in a modern office, dark slate overlay"></div>
  <h2 class="section-title">SERVICES</h2>
  <p class="section-sub">Lorem Ipsum is simply dummy text of the printing and typesetting industry</p>
</section>

<!-- Services -->
<section class="slide services-slide col-right row-2">
  <div class="brand-mini">KEYSTONE LANE<br>GAUGING</div>
  <div class="head-divider"></div>
  <h2 class="head-title">SERVICES</h2>

  <article class="service-card" style="left:9px;top:52px;height:85px">
    <span class="service-icon"><svg width="10" height="10" viewBox="0 0 10 10"><circle cx="5" cy="4" r="2.6" fill="none" stroke="#fff" stroke-width="1"/><path d="M3.8 7h2.4M4 8.6h2" stroke="#fff" stroke-width="1"/></svg></span>
    <h3>Lorem Ipsum</h3>
    <p>Truck scale sales, installation and certification for quarries, yards and weigh stations, backed by load cell testing and clear reports for every site we support.</p>
  </article>
  <article class="service-card" style="left:149px;top:52px;height:85px">
    <span class="service-icon"><svg width="10" height="10" viewBox="0 0 10 10"><path d="M2 2 8 3 7 8 2.5 7.5Z" fill="none" stroke="#fff" stroke-width=".9"/><circle cx="2" cy="2" r="1" fill="#fff"/><circle cx="8" cy="3" r="1" fill="#fff"/><circle cx="7" cy="8" r="1" fill="#fff"/><circle cx="2.5" cy="7.5" r="1" fill="#fff"/></svg></span>
    <h3>Lorem Ipsum</h3>
    <p>Floor scale supply and setup for warehouses and plants, including platform leveling, indicator wiring, ramp fitting and a full accuracy check before handover to staff.</p>
  </article>
  <article class="service-card" style="left:290px;top:52px;height:58px">
    <span class="service-icon"><svg width="10" height="10" viewBox="0 0 10 10"><rect x="2.2" y="1" width="5.6" height="8" fill="none" stroke="#fff" stroke-width="1"/><path d="M3.5 3h3M3.5 4.6h3M3.5 6.2h2" stroke="#fff" stroke-width=".8"/></svg></span>
    <h3>Lorem Ipsum</h3>
    <p>Routine calibration with traceable test weights, so every scale stays within tolerance.</p>
  </article>
  <article class="service-card" style="left:9px;top:144px;height:85px">
    <span class="service-icon"><svg width="10" height="10" viewBox="0 0 10 10"><circle cx="5" cy="5" r="2.2" fill="none" stroke="#fff" stroke-width="1.1"/><path d="M5 .8v1.6M5 7.6v1.6M.8 5h1.6M7.6 5h1.6M2 2l1.1 1.1M6.9 6.9 8 8M8 2 6.9 3.1M3.1 6.9 2 8" stroke="#fff" stroke-width="1.1"/></svg></span>
    <h3>Lorem Ipsum</h3>
    <p>Field service and repair for all scale types, with fast diagnosis, spare parts on hand and technicians who keep your lines weighing.</p>
  </article>
  <article class="service-card" style="left:149px;top:144px;height:85px">
    <span class="service-icon"><svg width="10" height="10" viewBox="0 0 10 10"><circle cx="3" cy="3.5" r="1.5" fill="#fff"/><circle cx="7" cy="3.5" r="1.5" fill="#fff"/><path d="M.5 8.5a2.5 2.5 0 0 1 5 0ZM4.5 8.5a2.5 2.5 0 0 1 5 0Z" fill="#fff"/></svg></span>
    <h3>Lorem Ipsum</h3>
    <p>Counting and benchtop scales for parts rooms and labs, sized to your loads and set up with the units and limits your team uses.</p>
  </article>
  <article class="service-card" style="left:290px;top:118px;height:111px">
    <span class="service-icon"><svg width="10" height="10" viewBox="0 0 10 10"><path d="M5 8.8 1.4 5.2a2 2 0 0 1 3.6-2.4 2 2 0 0 1 3.6 2.4Z" fill="#fff"/></svg></span>
    <h3>Lorem Ipsum</h3>
    <p>Service agreements that bundle planned calibration, priority repair and yearly inspection into one plan, with clear pricing, shared records and a named contact for each site, so compliance stays simple and downtime stays low across every location.</p>
  </article>
</section>

<!-- About -->
<section class="slide about-slide col-left row-3">
  <div class="brand-mini">KEYSTONE LANE<br>GAUGING</div>
  <div class="head-divider"></div>
  <h2 class="head-title">ABOUT US</h2>
  <p class="about-copy" style="top:57px">Keystone Lane Gauging sells, calibrates, services and repairs industrial and commercial scales of every type. Our teams work with truck scales, floor scales, counting scales and benchtop scales, supporting customers in manufacturing, logistics, agriculture and retail. Each job follows documented procedures and uses traceable test weights, so results hold up to audits and inspections. We keep parts in stock, plan visits around production schedules and report findings in plain terms that managers and operators can act on right away.</p>
  <p class="about-copy" style="top:145px">Three affiliated businesses extend our reach across the region, sharing technicians, equipment and training. Together we serve hundreds of sites, from single benchtop units to multi-deck truck scales at busy yards. The board's focus this year is steady growth in service contracts, faster response times and careful investment in new calibration capacity. This meeting reviews our results, the risks ahead and the roadmap that will guide the next twelve months of work for the whole group.</p>
  <div class="about-photo" role="img" aria-label="Photo of a business team meeting at a table in a bright glass-walled office"></div>
</section>

<!-- Process -->
<section class="slide process-slide col-right row-3">
  <div class="brand-mini">KEYSTONE LANE<br>GAUGING</div>
  <div class="head-divider"></div>
  <h2 class="head-title">PROCESS</h2>
  <svg class="process-line" width="434" height="244" viewBox="0 0 434 244">
    <path d="M20 61H380A43 43 0 0 1 380 147H20" fill="none" stroke="#3b434b" stroke-width="0.8"/>
  </svg>
  <div class="step-badge" style="left:29px;top:61px">01</div>
  <div class="step-badge" style="left:149px;top:61px">02</div>
  <div class="step-badge" style="left:274px;top:61px">03</div>
  <div class="step-badge" style="left:29px;top:147px">06</div>
  <div class="step-badge" style="left:149px;top:147px">05</div>
  <div class="step-badge" style="left:274px;top:147px">04</div>
  <div class="step" style="left:25px;top:90px"><h4>Discovery</h4><p>We review each site, its scales and its workloads to understand what the team needs to weigh.</p></div>
  <div class="step" style="left:147px;top:90px"><h4>Design</h4><p>We choose capacity, platform size and indicators, then plan the foundation and layout with your staff.</p></div>
  <div class="step" style="left:271px;top:90px"><h4>Development</h4><p>Scales are built, wired and fitted on site, with load cells matched and checked before use.</p></div>
  <div class="step" style="left:25px;top:175px"><h4>Retainer</h4><p>Planned calibration and priority repair keep every scale accurate, certified and in daily use.</p></div>
  <div class="step" style="left:147px;top:175px"><h4>Launch</h4><p>The scale goes live, operators are trained and certificates are handed over with full records.</p></div>
  <div class="step" style="left:271px;top:175px"><h4>QA</h4><p>Traceable test weights confirm accuracy across the range, and results are recorded for audits.</p></div>
</section>

<!-- Feature -->
<section class="slide feature-slide col-left row-4">
  <div class="brand-mini">KEYSTONE LANE<br>GAUGING</div>
  <div class="head-divider"></div>
  <h2 class="head-title">HEADING</h2>
  <div class="feature-rail"></div>
  <h3 class="feature-title">Collaboration<strong>Opportunity</strong></h3>
  <ul class="feature-points">
    <li>Lorem ipsum dolor sit amet, consectetur adipiscing elit, sed do eiusmod tempor</li>
    <li>Sed ut perspiciatis unde omnis iste natus error sit voluptatem accusantium doloremque</li>
    <li>But I must explain to you how all this mistaken idea of denouncing</li>
    <li>At vero eos et accusamus et iusto odio dignissimos ducimus</li>
  </ul>
  <svg class="feature-photo" width="434" height="244" viewBox="0 0 434 244" role="img" aria-label="Photo of two colleagues working together at a laptop in a dim office">
    <defs>
      <linearGradient id="featureTone" x1="0" y1="0" x2="1" y2="1">
        <stop offset="0" stop-color="#5a6470"/>
        <stop offset=".55" stop-color="#2f3a46"/>
        <stop offset="1" stop-color="#141b24"/>
      </linearGradient>
    </defs>
    <path d="M309 0H434V244H306Q168 122 309 0Z" fill="url(#featureTone)"/>
  </svg>
</section>

<!-- Closing -->
<section class="slide closing-slide col-right row-4">
  <div class="mesh-fade"></div>
  <div class="brand-mark">KEYSTONE LANE GAUGING</div>
  <h2 class="thanks">THANK <span>YOU</span></h2>
</section>

</body>
</html>
```